International Petrochemical business needs a web design for Clearway Desk system

We need a web design for a "Clearway Desk" system for an international petrochemical company. The web site is used internally within the company. It is hosted by an internal department which provides government permit request service for other departments.

We would like to see designs of two pages using color light blue. (home page, internal page as attached).
Home Page:
1. Header has a background image and small animation. Header on home page can be taller than the header of the internal page.
2. Layout as attached.

Internal Page:
1. Header can use the same background image as the home page and can be shorter to utilize the page for content.
2. The blue icon behind every captions represent an icon. When user move mouse over this icon, it displays the caption in Thai language as a tooltip. This icon needs to be redesign.

The final design should communicate the followings:
- Excellent service provided system in terms of time and accurary
- Rapid growth of business via building petrochemical refinery plant
Updates

For Internal Page, the blue circle behind every captions represent an icon. When mouse over this icon, a tool tip showing the caption in Thai language is shown. Please also design this icon..

There are more feedbacks from customer as followed:

1. Banner should consists of 
    1.1 "Approved" stamp on paper
    1.2 An image of Garuda. It is used on every government documents in Thailand
    1.3 Image of petrochemical plant
2. Each menu item (Home, Permit, Search, etc) should have different colors. Drop down menu will use the same color as its parent menu item.
3. Overall tone of the web page should be light blue with background of the body the web page in white
4. "New Request" button should use green color with icon on it
5. Table header of each box in the body of the page should use dark blue background with text in white

Please kindly submit your revisions.
Thank you.

Industry/Entity Type

Business

Requirements
Must have
• 1. Design for 1024x768 screen resolution
2. Use light blue theme
3. Background of header where the company logo is must have white background

```html
<!DOCTYPE html>
<html lang="en">
<head>
<meta charset="utf-8">
<title>Clearway Desk – Home</title>
<link href="https://fonts.googleapis.com/css2?family=PT+Sans+Narrow:wght@400;700&family=Source+Sans+3:wght@400;600&family=Sarabun:wght@400&display=swap" rel="stylesheet">
<style>
  :root{
    --sky:#12a9e6;
    --sky-dark:#0a8fcc;
    --sky-pale:#dcf1fb;
    --row:#efefef;
    --ink:#2f2f2f;
    --ink-soft:#444;
    --brand-ink:#1f3f66;
    --nav-active:#5a5a5a;
    --dropdown:#3db8ec;
    --panel-line:#dcdcdc;
    --white:#ffffff;
    --danger:#d90f0f;
    --warn:#f2dc14;
  }
  *{box-sizing:border-box;margin:0;padding:0}
  html,body{width:1010px;height:1200px;overflow:hidden}
  body{position:relative;background:linear-gradient(#f7f7f7,#e6e6e6);font-family:"Source Sans 3",sans-serif;color:var(--ink)}
  .site-header{position:absolute;left:0;top:0;width:1010px;height:72px;background:var(--white)}
  .brand{position:absolute;left:82px;top:25px;font-family:"Source Sans 3",sans-serif;font-weight:600;font-size:19px;line-height:22px;color:var(--brand-ink)}
  .main-nav{position:absolute;left:0;top:72px;width:1010px;height:44px;background:linear-gradient(var(--sky),#1fb0ea)}
  .nav-item{position:absolute;top:0;height:44px;line-height:44px;font-family:"PT Sans Narrow",sans-serif;font-weight:700;font-size:17px;color:var(--white)}
  .nav-item.active{background:var(--nav-active);text-align:center}
  .nav-sep{position:absolute;top:2px;width:1px;height:40px;background:rgba(255,255,255,.35)}
  .dropdown{position:absolute;left:153px;top:116px;width:165px;height:88px;background:var(--dropdown);border-radius:0 0 4px 4px;padding:8px 18px;z-index:3}
  .dropdown a{display:block;font-family:"PT Sans Narrow",sans-serif;font-weight:700;font-size:16px;line-height:26px;color:var(--white);text-decoration:none}
  .hero{position:absolute;left:0;top:116px;width:1010px;height:222px;background:linear-gradient(#9fc3e0 0%,#c9ddec 50%,#6f7a80 78%,#3e464c 100%)}
  .hero-arrow{position:absolute;top:73px;width:38px;height:38px;border-radius:50%;background:rgba(255,255,255,.7)}
  .panel{position:absolute;background:var(--white);border:1px solid var(--panel-line);border-radius:4px;padding:6px;box-shadow:0 1px 2px rgba(0,0,0,.06)}
  .panel-title{height:41px;line-height:43px;background:var(--sky);border-radius:3px;color:var(--white);font-family:"PT Sans Narrow",sans-serif;font-weight:700;font-size:20px;padding-left:14px}
  .grid{display:grid;align-items:center;padding-left:14px}
  .table-head{height:28px;margin-top:3px;background:var(--sky-pale);font-family:"PT Sans Narrow",sans-serif;font-weight:700;font-size:17px;color:var(--ink-soft)}
  .table-row{height:27px;margin-top:3px;background:var(--row);font-size:13px}
  .thai{font-family:"Sarabun",sans-serif;font-size:13px}
  .pager{position:absolute;right:14px;bottom:8px;font-size:13px;display:flex;align-items:center;gap:6px}
  .pager .current{width:17px;height:17px;border-radius:50%;background:var(--sky);color:var(--white);text-align:center;line-height:17px;font-size:12px}
  .cols-3{grid-template-columns:141px 141px 1fr}
  .cols-wr{grid-template-columns:121px 130px 1fr}
  .cols-exp{grid-template-columns:121px 131px 171px 111px 145px 1fr}
  .cols-ip{grid-template-columns:121px 141px 1fr}
  .cols-done{grid-template-columns:161px 1fr}
  .days{display:flex;justify-content:flex-end;align-items:center;gap:10px}
  .dot{width:18px;height:18px;border-radius:50%}
  .dot.red{background:radial-gradient(circle at 35% 35%,#ff5a5a,var(--danger))}
  .dot.yellow{background:radial-gradient(circle at 35% 35%,#fff59a,var(--warn))}
  .due{padding-left:30px}
  .action-panel .new-request{display:block;height:68px;line-height:62px;background:var(--sky);border-radius:3px;color:var(--white);text-align:center;font-family:"PT Sans Narrow",sans-serif;font-weight:700;font-size:20px;text-decoration:none}
  .site-footer{position:absolute;left:0;top:1089px;width:1010px;height:111px;background:linear-gradient(90deg,#1b3150 0%,#3a3f4a 30%,#6a4a2c 55%,#2c3a55 80%,#1d3150 100%);border-top:3px solid var(--sky-dark)}
  .social{position:absolute;left:89px;top:35px;display:flex;gap:12px}
  .social span{width:26px;height:26px;border-radius:3px;background:#3b8fd0}
  .footer-meta{position:absolute;right:71px;top:20px;text-align:right;color:var(--white);font-size:11px;line-height:18px}
  .footer-meta a{color:var(--white);text-decoration:none}
</style>
</head>
<body>
  <header class="site-header">
    <div class="brand">Northbay Refining</div>
  </header>

  <nav class="main-nav">
    <span class="nav-item" style="left:92px">Home</span>
    <span class="nav-item active" style="left:153px;width:114px">Permits</span>
    <span class="nav-item" style="left:286px">Search</span>
    <span class="nav-sep" style="left:354px"></span>
    <span class="nav-item" style="left:381px">Report</span>
    <span class="nav-sep" style="left:455px"></span>
    <span class="nav-item" style="left:476px">Admin</span>
    <span class="nav-sep" style="left:534px"></span>
    <span class="nav-item" style="left:564px">Help</span>
  </nav>
  <div class="dropdown">
    <a href="#">Create New Permit</a>
    <a href="#">Transfer Role</a>
    <a href="#">Transfer Res.Person</a>
  </div>

  <div class="hero" role="img" aria-label="Petrochemical refinery plant with towers and chimneys under a pale sky">
    <span class="hero-arrow" style="left:33px"></span>
    <span class="hero-arrow" style="left:929px"></span>
  </div>

  <section class="panel" style="left:81px;top:368px;width:402px;height:190px">
    <div class="panel-title">New Requests</div>
    <div class="grid cols-3 table-head"><span>Request No</span><span>Request Date</span><span>Branch</span></div>
    <div class="grid cols-3 table-row"><span>56-0003</span><span>20/4/2013</span><span>Gc1</span></div>
    <div class="grid cols-3 table-row"><span>56-0004</span><span>21/4/2013</span><span>Gc1</span></div>
    <div class="pager"><span class="current">1</span>2 3 4</div>
  </section>

  <section class="panel" style="left:526px;top:368px;width:403px;height:190px">
    <div class="panel-title">My Working Requests</div>
    <div class="grid cols-wr table-head"><span>Request No</span><span>Request Date</span><span>Status</span></div>
    <div class="grid cols-wr table-row"><span>56-0200</span><span>25/3/2013</span><span>Waiting for Process</span></div>
    <div class="grid cols-wr table-row"><span>55-0210</span><span>24/3/2013</span><span>In Progress</span></div>
    <div class="grid cols-wr table-row"><span>55-0301</span><span>18/1/2013</span><span>Cancel Requested</span></div>
    <div class="pager" style="bottom:4px"><span class="current">1</span>2 3 4</div>
  </section>

  <section class="panel" style="left:81px;top:581px;width:849px;height:166px">
    <div class="panel-title">Expiring Permits</div>
    <div class="grid cols-exp table-head"><span>Request No</span><span>Expire&nbsp; Date</span><span>Permit Name</span><span>Branch</span><span>Required Time (Day)</span><span>Due Date</span></div>
    <div class="grid cols-exp table-row"><span>AB56001</span><span>25/3/2013</span><span>Permit Name ###10</span><span>GC1</span><span class="days">30 <i class="dot red"></i></span><span class="due">-40</span></div>
    <div class="grid cols-exp table-row"><span>B105502</span><span>24/3/2013</span><span>Permit Name ###10</span><span>GC2</span><span class="days">60 <i class="dot yellow"></i></span><span class="due">15</span></div>
    <div class="pager"><span class="current">1</span>2 3 4</div>
  </section>

  <section class="panel" style="left:81px;top:769px;width:402px;height:292px">
    <div class="panel-title">My In Progress Requests</div>
    <div class="grid cols-ip table-head"><span>Request No</span><span>Request Date</span><span>Status</span></div>
    <div class="grid cols-ip table-row"><span>56-0003</span><span>20/4/2013</span><span class="thai">ระหว่างดำเนินการ</span></div>
    <div class="grid cols-ip table-row"><span>56-0004</span><span>21/4/2013</span><span class="thai">รอดำเนินการ</span></div>
    <div class="pager"><span class="current">1</span>2 3 4</div>
  </section>

  <section class="panel action-panel" style="left:529px;top:769px;width:403px;height:80px">
    <a class="new-request" href="#">New Requests</a>
  </section>

  <section class="panel" style="left:529px;top:869px;width:403px;height:191px">
    <div class="panel-title">Recent Completed Requests</div>
    <div class="grid cols-done table-head"><span>Request No</span><span>Completed Date</span></div>
    <div class="grid cols-done table-row"><span>55-0100</span><span>25/3/2013</span></div>
    <div class="grid cols-done table-row"><span>55-0088</span><span>24/3/2013</span></div>
    <div class="grid cols-done table-row"><span>55-0002</span><span>18/1/2013</span></div>
    <div class="pager" style="bottom:4px"><span class="current">1</span>2 3 4</div>
  </section>

  <footer class="site-footer" role="img" aria-label="Refinery plant lit up at night">
    <div class="social"><span></span><span></span><span></span><span></span><span></span><span></span></div>
    <div class="footer-meta">
      <a href="#">FAQ</a> &nbsp;|&nbsp; <a href="#">Terms</a> &nbsp;|&nbsp; <a href="#">Privacy</a><br>
      © 2013 Northbay Refining, All rights reserved<br>
      x2
    </div>
  </footer>
</body>
</html>
```